Money Mindset Podcast needs fun, creative cover art

Launching a new podcast called 'Turning Your Thoughts Toward Savings' - aimed at an audience 30-50 who are interested in the practicalities of managing their money but also the more mental and emotional aspects.
Looking for something not too serious, warm and friendly.

Must be easy to read on phone screens
3000 x 3000 in size
Avoid currency symbols $, £ etc, as may have an international audience

Target Market(s)

Podcast listeners age 30-50 starting in the UK but then worldwide. Probably 60:40 female bias

Industry/Entity Type

Life Coaching

Font styles to use
Serif
Sans Serif

Colors
cadf82
fee18a
acd037
85cae6
eea4c8
f59195
85acd3

Requirements
Must have
• Simple, clear design. Easy to read on variety of devices. 3000 x 3000
Appeal to those with a spiritual or emotional interests
Nice to have
• Stand out among other money related podcasts
Maybe play around with clouds, lightbulbs and clearing skies
Should not have
• Currency symbols such as $ or £
Be too corporate or bank like
Stock images

```html
<!DOCTYPE html>
<html lang="en">
<head>
<meta charset="utf-8">
<title>Turning Your Thoughts Toward Savings – Podcast Cover</title>
<link rel="stylesheet" href="https://fonts.googleapis.com/css2?family=Delius&display=swap">
<style>
  :root {
    --coral: #f59195;
    --blush: #eea4c8;
    --sun: #fee18a;
    --lime: #cadf82;
    --sky: #85cae6;
    --cream: #fffdf4;
  }
  html, body {
    margin: 0;
    padding: 0;
    width: 1200px;
    height: 1200px;
    overflow: hidden;
    background: var(--coral);
  }
  .cover {
    position: relative;
    width: 1200px;
    height: 1200px;
    background: var(--coral);
    overflow: hidden;
    font-family: "Delius", "Comic Sans MS", sans-serif;
    color: var(--cream);
  }
  .burst-area {
    position: absolute;
    inset: 0;
    background:
      radial-gradient(circle at 50% 50%,
        rgba(245, 145, 149, 0) 0,
        rgba(245, 145, 149, 0) 40%,
        rgba(254, 225, 138, 0.45) 58%,
        rgba(238, 164, 200, 0.55) 78%,
        rgba(133, 202, 230, 0.35) 100%);
  }
  .title {
    position: absolute;
    inset: 0;
    margin: 0;
    display: flex;
    flex-direction: column;
    align-items: center;
    justify-content: center;
    text-align: center;
    font-weight: 400;
    line-height: 1;
    padding-bottom: 40px;
    box-sizing: border-box;
  }
  .title span { display: block; }
  .title .line-small {
    font-size: 72px;
    letter-spacing: 4px;
    margin-bottom: 16px;
  }
  .title .line-tiny {
    font-size: 60px;
    letter-spacing: 3px;
    margin-bottom: 6px;
  }
  .title .line-big {
    font-size: 128px;
    letter-spacing: 2px;
  }
  .title .line-lower {
    font-size: 76px;
    margin: 10px 0 6px;
  }
</style>
</head>
<body>
<main class="cover">
  <div class="burst-area" role="img" aria-label="Hand-drawn sunburst of light rays radiating outward around the title"></div>
  <h1 class="title">
    <span class="line-small">TURNING</span>
    <span class="line-tiny">YOUR</span>
    <span class="line-big">THOUGHTS</span>
    <span class="line-lower">toward</span>
    <span class="line-big">SAVINGS</span>
  </h1>
</main>
</body>
</html>
```